Business Card for Field Bloom-Eco Friendly Organic Clothing Brand

We are looking for an amazing business card for our eco friendly, organic clothing brand. We are thinking maybe a business card with a peel off sticker on the back, since our hanging clothing tag is a peel off sticker on the back. I will attach our hang tag so we can make sure we stay in line with our design. I've also attached a bag we are doing because I do like the scattered emblem look as well.

```html
<!DOCTYPE html>
<html lang="en">
<head>
<meta charset="utf-8">
<title>Field Bloom Business Card</title>
<link rel="stylesheet" href="https://fonts.googleapis.com/css2?family=Open+Sans:wght@400;700&display=swap">
<style>
  :root {
    --backdrop: #2f2a28;
    --paper: #fbfbfa;
    --ink: #1c1c1c;
    --ink-soft: #2e2e2e;
    --tag-dark: #1f1f17;
    --gold-light: #e6c873;
    --gold-mid: #cfa846;
    --gold-deep: #b48a2c;
    --white: #ffffff;
  }
  * { box-sizing: border-box; margin: 0; padding: 0; }
  html, body {
    width: 1200px;
    height: 844px;
    overflow: hidden;
    background: var(--backdrop);
    font-family: "Open Sans", Arial, sans-serif;
  }
  .canvas {
    position: relative;
    width: 1200px;
    height: 844px;
  }
  .card {
    position: absolute;
    top: 274px;
    width: 520px;
    height: 297px;
    border-radius: 4px;
    box-shadow: 0 14px 30px rgba(0,0,0,0.45);
    overflow: hidden;
  }
  /* Front */
  .card-front {
    left: 60px;
    background: var(--paper);
    color: var(--ink);
  }
  .brand-tag {
    position: absolute;
    top: 30px;
    right: 30px;
    width: 210px;
    height: 78px;
    background: var(--tag-dark);
    border-radius: 10px;
    padding: 14px 18px;
    display: flex;
    align-items: center;
    gap: 12px;
  }
  .brand-tag .brand-square {
    width: 34px;
    height: 34px;
    background: var(--gold-mid);
    flex: none;
  }
  .brand-tag .brand-text {
    display: flex;
    flex-direction: column;
    gap: 4px;
  }
  .brand-tag .brand-name {
    font-weight: 700;
    font-size: 20px;
    color: var(--gold-light);
    line-height: 1;
  }
  .brand-tag .brand-url {
    font-size: 9px;
    color: var(--gold-light);
    line-height: 1;
  }
  .person {
    position: absolute;
    left: 34px;
    top: 150px;
  }
  .person-name {
    font-weight: 700;
    font-size: 17px;
    line-height: 1.2;
  }
  .person-title {
    font-size: 13px;
    color: var(--ink-soft);
  }
  .contact {
    position: absolute;
    left: 34px;
    top: 210px;
    font-size: 13px;
    line-height: 1.55;
    color: var(--ink);
  }
  .contact .address { margin-bottom: 14px; }
  /* Back */
  .card-back {
    left: 620px;
    background: linear-gradient(135deg, var(--gold-light) 0%, var(--gold-mid) 55%, var(--gold-deep) 100%);
  }
  .back-brand {
    position: absolute;
    top: 62px;
    right: 40px;
    text-align: right;
    color: var(--white);
  }
  .back-brand .brand-name {
    font-weight: 700;
    font-size: 40px;
    line-height: 1;
  }
  .back-brand .brand-url {
    margin-top: 12px;
    font-size: 14px;
  }
</style>
</head>
<body>
<main class="canvas">
  <section class="card card-front" aria-label="Card front">
    <div class="brand-tag">
      <span class="brand-square"></span>
      <div class="brand-text">
        <span class="brand-name">Field Bloom</span>
        <span class="brand-url">www.fieldbloom.com</span>
      </div>
    </div>
    <div class="person">
      <p class="person-name">John Smith</p>
      <p class="person-title">Managing Director</p>
    </div>
    <div class="contact">
      <p class="address">1234, Address GoesHere, Country, 12345</p>
      <p>T:(044) 123 456 789&nbsp; F:(044) 123456789&nbsp; M:(044)123456789</p>
      <p>E:info@youremail.com&nbsp;&nbsp; www.yourweb.com</p>
    </div>
  </section>

  <section class="card card-back" aria-label="Card back">
    <div class="back-brand">
      <p class="brand-name">Field Bloom</p>
      <p class="brand-url">www.fieldbloom.com</p>
    </div>
  </section>
</main>
</body>
</html>
```